Corvane Holdings , new business card design

investment firm with corporate clients . need double sided business card , vertical and horizontal options ,logo must be clear. prefer pantone colors only and sharp design. website also www.corvane.ae

Khalid Bin Tarrafi
Managing Director
Tel. +971 4 387 2940
Mobile +971 50 518 2403
khalid@corvane.ae
Q-Span Plaza, officw 18-B07, Warqa Gardens, Dubai

Contact Information for Business Card

Khalid Bin Tarrafi
Managing Director

Font styles to use
Serif

Colors

Designer to choose colors to be used in the design.

```html
<!DOCTYPE html>
<html lang="en">
<head>
<meta charset="utf-8">
<title>Corvane Holdings – Business Card</title>
<link href="https://fonts.googleapis.com/css2?family=Lato:wght@300;400&display=swap" rel="stylesheet">
<style>
  :root {
    --bg: #e9e7e4;
    --card: #fbfbfa;
    --ink: #1f1f22;
    --rule: #4a4a4e;
    --brand: #41709a;
  }
  * { margin: 0; padding: 0; box-sizing: border-box; }
  html, body { width: 1200px; height: 1200px; overflow: hidden; }
  body {
    background: var(--bg);
    font-family: "Lato", Arial, sans-serif;
    color: var(--ink);
    position: relative;
  }
  .card {
    position: absolute;
    left: 180px;
    width: 840px;
    height: 480px;
    background: var(--card);
    box-shadow: 0 6px 18px rgba(0,0,0,0.12);
  }
  .card--front { top: 90px; }
  .card--back { top: 630px; }

  /* Front */
  .brand {
    display: flex;
    align-items: center;
    gap: 14px;
    font-weight: 300;
    color: var(--ink);
    letter-spacing: 0.12em;
    text-transform: uppercase;
  }
  .brand__mark {
    width: 16px;
    height: 16px;
    background: var(--brand);
    flex: none;
  }
  .card--front .brand {
    position: absolute;
    left: 50%;
    top: 50%;
    transform: translate(-50%, -50%);
    font-size: 40px;
    white-space: nowrap;
  }

  /* Back */
  .identity {
    position: absolute;
    left: 40px;
    top: 40px;
    width: 170px;
    height: 400px;
    display: flex;
    flex-direction: row;
    justify-content: center;
    gap: 22px;
  }
  .identity__col {
    writing-mode: vertical-rl;
    transform: rotate(180deg);
    display: flex;
    align-items: center;
    justify-content: center;
    white-space: nowrap;
  }
  .identity .brand {
    font-size: 30px;
    writing-mode: vertical-rl;
  }
  .identity .brand__mark { width: 12px; height: 12px; }
  .website { font-size: 19px; font-weight: 400; letter-spacing: 0.02em; }

  .divider-v {
    position: absolute;
    left: 232px;
    top: 40px;
    width: 1px;
    height: 400px;
    background: var(--rule);
  }
  .details {
    position: absolute;
    left: 232px;
    top: 40px;
    right: 40px;
    bottom: 40px;
  }
  .person { padding: 30px 0 0 30px; height: 120px; }
  .person__name { font-size: 38px; font-weight: 400; line-height: 1.1; }
  .person__title { font-size: 21px; font-weight: 400; margin-top: 4px; }
  .rule-h { height: 1px; background: var(--rule); }
  .contact {
    display: grid;
    grid-template-columns: 92px 20px auto;
    row-gap: 4px;
    padding: 22px 0 22px 30px;
    font-size: 25px;
    line-height: 1.15;
  }
  .address {
    padding: 22px 0 0 30px;
    font-size: 19px;
    line-height: 1.35;
  }
</style>
</head>
<body>

<section class="card card--front" aria-label="Business card front">
  <div class="brand"><span class="brand__mark"></span>Corvane Holdings</div>
</section>

<section class="card card--back" aria-label="Business card back">
  <div class="identity">
    <div class="identity__col">
      <div class="brand"><span class="brand__mark"></span>Corvane Holdings</div>
    </div>
    <div class="identity__col">
      <span class="website">www.corvane.ae</span>
    </div>
  </div>

  <div class="divider-v"></div>

  <div class="details">
    <div class="person">
      <div class="person__name">Khalid Bin Tarrafi</div>
      <div class="person__title">Managing Director</div>
    </div>
    <div class="rule-h"></div>
    <div class="contact">
      <span>Tel</span><span>:</span><span>+971 4 387 2940</span>
      <span>Mobile</span><span>:</span><span>+971 50 518 2403</span>
      <span>Email</span><span>:</span><span>khalid@corvane.ae</span>
    </div>
    <div class="rule-h"></div>
    <div class="address">
      Q-Span Plaza, officw 18-B07,<br>
      Warqa Gardens, Dubai
    </div>
  </div>
</section>

</body>
</html>
```